VORLAND COMPOSITES INC website in USA

VORLAND COMPOSITES INC incorporated and operated in USA needs a completely new design of website. This Wyoming based company is a importer and distributor of composites material to supply mainly to American and Canadian/Mexican customers. Our main products includes Carbon Fiber, Aramid Fiber, Glass Fiber, Basalt Fiber, High Silica Glass, Quartz Fiber, S-Glass, Alumina Fiber, Vacuum Auxiliary.

We are one stop composites solution provider for Automotive, Aerospace, Construction, Electrical and Machinery industries.

We are exclusive sales company in North America for BLORAN composites produced from China and their other Asia facilities.

Target Market(s)

USA and Canada

Industry/Entity Type

Composites materials

Coding

Coded - Design and coding required

Number of Pages Required

5+ page

Requirements
Nice to have
• Color theme to match our corporate logo VORLAND. VORLAND stands for Northgate Provisioning Trade Holdings

```html
<!DOCTYPE html>
<html lang="en">
<head>
<meta charset="utf-8">
<title>VORLAND Composites Inc</title>
<link href="https://fonts.googleapis.com/css2?family=Oswald:wght@600;700&family=Poppins:wght@400;500;600&display=swap" rel="stylesheet">
<style>
:root{
  --orange:#f39430;
  --ink:#1d1d1d;
  --text:#3c3c3c;
  --muted:#8a8a8a;
  --grey:#ececec;
  --dark:#2e2e2e;
  --blue-dark:#1c3350;
  --blue:#3f6a98;
  --white:#fff;
}
*{margin:0;padding:0;box-sizing:border-box}
html,body{width:1200px;height:3876px;overflow:hidden}
body{position:relative;background:var(--white);font-family:'Poppins',sans-serif;color:var(--text)}
.abs{position:absolute}
.display{font-family:'Oswald',sans-serif;font-weight:700;font-style:italic;text-transform:uppercase;letter-spacing:.5px}
.accent{color:var(--orange)}
.eyebrow{font-size:14px;color:var(--orange);text-transform:uppercase;letter-spacing:.3px}
.btn{display:inline-block;background:var(--orange);color:#fff;font-size:12.5px;line-height:16px;text-transform:uppercase;padding:12px 24px;border-radius:22px;position:relative}
.btn::after{content:"";position:absolute;right:-14px;top:8px;width:24px;height:24px;border:2px solid var(--orange);clip-path:polygon(50% 0,61% 35%,98% 35%,68% 57%,79% 91%,50% 70%,21% 91%,32% 57%,2% 35%,39% 35%);}

/* header */
.site-header{top:0;left:0;width:1200px;height:99px;background:#fff}
.brand{left:140px;top:22px;display:flex;align-items:center;gap:12px}
.brand-dot{width:16px;height:16px;border-radius:50%;background:var(--orange)}
.brand-name{font-family:'Oswald',sans-serif;font-weight:700;font-size:38px;color:var(--ink);line-height:1}
.brand-divider{width:1px;height:46px;background:var(--ink);margin-left:6px}
.brand-tag{font-size:10px;line-height:13px;color:var(--ink);width:100px;font-style:italic}
.nav{top:42px;left:583px;display:flex;gap:49px;font-size:12.5px;color:var(--ink)}
.nav .active{color:var(--orange)}
.call{left:914px;top:30px;display:flex;align-items:center;gap:12px}
.call-icon{width:36px;height:36px;border-radius:50%;background:var(--orange);display:flex;align-items:center;justify-content:center}
.call small{display:block;font-size:10px;color:var(--ink);font-weight:500}
.call strong{font-size:15px;color:var(--ink);font-weight:600}

/* hero */
.hero{top:99px;left:0;width:1200px;height:722px;overflow:hidden}
.hero-media{position:absolute;inset:0;background:radial-gradient(ellipse at 80% 45%,#5b86b4 0%,var(--blue) 28%,var(--blue-dark) 70%,#142739 100%)}
.hero-title{left:143px;top:152px;color:#fff;font-size:40px;line-height:50px}
.hero-copy{left:143px;top:258px;width:490px;color:#fff;font-size:18px;line-height:30px}
.hero-cta{left:142px;top:404px}
.hero-cut{left:0;top:580px}
.scroll-down{left:563px;top:588px;width:74px;height:74px;border-radius:50%;background:#fff;box-shadow:0 4px 12px rgba(0,0,0,.15);display:flex;align-items:center;justify-content:center}

/* about */
.about-frame{left:126px;top:1030px;width:270px;height:268px;border-left:14px solid var(--orange);border-bottom:14px solid var(--orange)}
.about-media{left:140px;top:854px;width:431px;height:430px;border-radius:16px;background:linear-gradient(135deg,#2a2a2a,#6b6b6b 45%,#1e1e1e 70%,#8c8c8c)}
.about-text{left:635px;top:884px;width:425px}
.about-text h2{font-size:45px;line-height:54px;color:var(--ink);margin:4px 0 10px}
.about-text p{font-size:13.5px;line-height:23px;color:var(--text);margin-bottom:10px}
.about-text .btn{margin-top:18px}

/* products */
.products-bg{left:0;top:1380px}
.section-head{width:1200px;left:0;text-align:center}
.section-head h2{font-size:44px;line-height:54px;color:var(--ink);margin-top:2px}
.hex{width:218px;height:250px;clip-path:polygon(50% 0,100% 25%,100% 75%,50% 100%,0 75%,0 25%)}
.hex::before{content:"";position:absolute;inset:0;background:linear-gradient(180deg,rgba(0,0,0,0) 40%,rgba(0,0,0,.55) 100%)}
.hex-label{position:absolute;left:0;right:0;top:178px;text-align:center;color:#fff;font-family:'Oswald',sans-serif;font-weight:600;font-style:italic;font-size:19px;text-shadow:0 1px 4px rgba(0,0,0,.8)}

/* industries */
.industries{left:0;top:2410px;width:1200px;height:600px}
.hub{left:480px;top:94px;width:240px;height:240px;border-radius:50%;background:#fff;box-shadow:0 8px 30px rgba(0,0,0,.1);display:flex;align-items:center;justify-content:center;gap:8px}
.hub .brand-name{font-size:40px}
.sector-label{font-family:'Oswald',sans-serif;font-weight:600;font-style:italic;font-size:19px;fill:var(--ink)}

/* contact */
.contact-info{left:143px;top:3118px;width:420px}
.contact-info h2{font-size:44px;line-height:54px;color:var(--ink)}
.contact-info .lead{font-size:13.5px;margin-top:2px}
.info-item{display:flex;gap:22px;margin-top:30px;align-items:flex-start}
.info-icon{width:64px;height:64px;border-radius:50%;background:#fff;box-shadow:0 4px 16px rgba(0,0,0,.1);display:flex;align-items:center;justify-content:center;flex:none}
.info-item h3{font-size:17px;font-weight:500;color:var(--ink);margin-top:4px}
.info-item p{font-size:13.5px;line-height:22px}
.partners{left:143px;top:3518px;display:flex;align-items:center;gap:34px}
.partners span{font-size:17px;font-weight:500;color:var(--ink)}
.partner-mark{display:flex;align-items:center;gap:8px;font-weight:600;font-size:24px;color:var(--ink)}
.partner-mark i{width:26px;height:26px;background:#5bb534;display:block}

.quick-contact{left:608px;top:3083px;width:451px;height:542px;background:#fff;border-top:5px solid var(--orange);border-radius:6px;box-shadow:0 6px 30px rgba(0,0,0,.12);padding:30px 28px}
.quick-contact h2{font-size:44px;line-height:50px;color:var(--ink);margin-bottom:22px}
.field{border-bottom:1px solid #ccc;padding-bottom:12px;margin-bottom:18px;position:relative}
.field label{font-size:13px;line-height:18px;color:var(--ink);display:block;margin-bottom:8px}
.field .ph{font-size:13px;line-height:18px;color:var(--muted);display:block}
.field .ico{position:absolute;right:0;top:30px;width:10px;height:10px;background:var(--orange);border-radius:2px}
.field.message{height:104px;margin-bottom:24px}

/* footer */
.footer-bg{left:0;top:3580px}
.footer-nav{left:143px;top:3730px;display:flex;gap:40px;font-size:13px;color:#fff;font-weight:500}
.footer-brand{left:465px;top:3705px;display:flex;align-items:center;gap:12px}
.footer-brand .brand-name{color:#fff}
.footer-brand .brand-divider{background:#fff}
.footer-brand .brand-tag{color:#fff}
.follow{left:848px;top:3726px;display:flex;align-items:center;gap:10px;color:#fff;font-size:13px;font-weight:500}
.follow i{display:block;width:24px;height:24px;border-radius:50%;border:1.5px solid #fff}
.follow i.on{background:var(--orange);border-color:var(--orange)}
.footer-rule{left:140px;top:3813px;width:920px;height:1px;background:#555}
.copyright{left:0;top:3835px;width:1200px;text-align:center;color:#ddd;font-size:12.5px}
</style>
</head>
<body>

<header class="abs site-header">
  <div class="abs brand">
    <span class="brand-dot"></span>
    <span class="brand-name">VORLAND</span>
    <span class="brand-divider"></span>
    <span class="brand-tag">Northgate Provisioning Trade Holdings</span>
  </div>
  <nav class="abs nav"><span class="active">HOME</span><span>PRODUCTS</span><span>CONTACT US</span></nav>
  <div class="abs call">
    <span class="call-icon"><svg width="16" height="16" viewBox="0 0 24 24"><path fill="#fff" d="M6.6 10.8a15 15 0 0 0 6.6 6.6l2.2-2.2c.3-.3.7-.4 1-.2 1.1.4 2.3.6 3.6.6.6 0 1 .4 1 1V20c0 .6-.4 1-1 1A17 17 0 0 1 3 4c0-.6.4-1 1-1h3.5c.6 0 1 .4 1 1 0 1.3.2 2.5.6 3.6.1.3 0 .7-.2 1z"/></svg></span>
    <div><small>CALL US TODAY</small><strong>555-208-3146</strong></div>
  </div>
</header>

<section class="abs hero">
  <div class="hero-media" role="img" aria-label="Close-up of a rolled dark blue perforated composite sheet"></div>
  <h1 class="abs display hero-title">Premium Composite<br>Materials for North America</h1>
  <p class="abs hero-copy">VORLAND is a leading importer and distributor of high-performance composite materials, serving the automotive, aerospace, construction, and electrical industries across the USA, Canada, and Mexico.</p>
  <a class="abs btn hero-cta">Contact us today</a>
  <svg class="abs hero-cut" width="1200" height="142" viewBox="0 0 1200 142">
    <polygon points="0,142 0,122 1200,30 1200,142" fill="#fff"/>
    <polygon points="0,120 0,142 200,84" fill="#c9c9c9"/>
    <polygon points="0,122 0,142 1200,142 1200,30 900,52" fill="#fff"/>
    <polygon points="880,52 1200,12 1200,142" fill="var(--orange)"/>
  </svg>
  <div class="abs scroll-down"><svg width="14" height="16" viewBox="0 0 14 16"><path d="M2 2l5 5 5-5M2 8l5 5 5-5" fill="none" stroke="#333" stroke-width="1.8"/></svg></div>
</section>

<section>
  <div class="abs about-frame"></div>
  <div class="abs about-media" role="img" aria-label="Rolls of woven carbon fiber fabric"></div>
  <div class="abs about-text">
    <div class="eyebrow">Who we serve</div>
    <h2 class="display">About <span>VOR</span><span class="accent">LAND</span></h2>
    <p>Duis autem vel eum iriure dolor in hendrerit in vulputate.</p>
    <p>Ut wisi enim ad minim veniam, quis nostrud exerci ta ullamcorper suscipit lobortis nisl ut aliquip ex ea commodo cquat. Duis autem vel eum iriure dolor in hendrerit in vulate velit esse tie consequat, vel illum dolore eu feugiat nulla facilisis at vero eros et accumsan et iusto odio dignissim qui blandit praesent.</p>
    <p>Lorem ipsum dolor sit amet, consectetuer adipiscing elit, sed diam nonummy nibh euismod tincidunt ut laoreet dolore magna aliquam erat volutpat.</p>
    <a class="btn">Contact us today</a>
  </div>
</section>

<section>
  <svg class="abs products-bg" width="1200" height="1000" viewBox="0 0 1200 1000">
    <polygon points="0,36 1200,0 1200,990 0,955" fill="var(--grey)"/>
  </svg>
  <div class="abs section-head" style="top:1497px">
    <div class="eyebrow">What we offer</div>
    <h2 class="display">Our <span class="accent">Products</span></h2>
  </div>
  <div class="abs hex" style="left:140px;top:1593px;background:linear-gradient(135deg,#222,#777 50%,#333)" role="img" aria-label="Carbon fiber weave"><span class="hex-label">Carbon Fiber</span></div>
  <div class="abs hex" style="left:374px;top:1593px;background:linear-gradient(135deg,#e8e39a,#b5ae48 60%,#8f8a3a)" role="img" aria-label="Yellow aramid fiber tape"><span class="hex-label">Aramid Fiber</span></div>
  <div class="abs hex" style="left:608px;top:1593px;background:linear-gradient(135deg,#b9bcbf,#7d8184 55%,#5e6265)" role="img" aria-label="Glass fiber cloth"><span class="hex-label">Glass Fiber</span></div>
  <div class="abs hex" style="left:842px;top:1593px;background:linear-gradient(135deg,#7a6148,#3e3024 55%,#5a4630)" role="img" aria-label="Basalt fiber mesh"><span class="hex-label">Basalt Fiber</span></div>
  <div class="abs hex" style="left:257px;top:1796px;background:linear-gradient(135deg,#5a4c44,#b8b5b0 55%,#8e8a86)" role="img" aria-label="High silica glass sleeves"><span class="hex-label">High Silica Glass</span></div>
  <div class="abs hex" style="left:491px;top:1796px;background:linear-gradient(135deg,#e9e9e9,#bdbdbd 55%,#6f6f6f)" role="img" aria-label="Quartz fiber braided sleeves"><span class="hex-label">Quartz Fiber</span></div>
  <div class="abs hex" style="left:725px;top:1796px;background:linear-gradient(135deg,#dcdcdc,#acacac 55%,#7d7d7d)" role="img" aria-label="S-glass yarn bobbins"><span class="hex-label">S-Glass</span></div>
  <div class="abs hex" style="left:374px;top:2000px;background:linear-gradient(135deg,#e8e8e8,#bcbcbc 55%,#737373)" role="img" aria-label="Alumina fiber cloth"><span class="hex-label">Alumina Fiber</span></div>
  <div class="abs hex" style="left:608px;top:2000px;background:linear-gradient(135deg,#f4f26a,#c8c92a 55%,#5f6b1c)" role="img" aria-label="Yellow vacuum bagging film"><span class="hex-label">Vacuum Auxiliary</span></div>
</section>

<section class="abs industries">
  <div class="abs section-head" style="top:10px">
    <div class="eyebrow">Sectors we serve</div>
    <h2 class="display">Industries <span class="accent">We Serve</span></h2>
  </div>
  <div class="abs hub"><span class="brand-dot"></span><span class="brand-name">VORLAND</span></div>
  <svg class="abs" style="left:0;top:0" width="1200" height="600" viewBox="0 0 1200 600">
    <g stroke-linejoin="round" stroke-width="24">
      <polygon points="356,226 442,226 452,240 420,326 360,326 350,300" fill="var(--orange)" stroke="var(--orange)"/>
      <polygon points="758,226 844,226 850,300 840,326 780,326 748,240" fill="var(--orange)" stroke="var(--orange)"/>
      <polygon points="422,340 480,322 532,366 514,420 480,430 420,394" fill="#111" stroke="#111"/>
      <polygon points="778,322 720,340 686,380 704,430 770,410 786,370" fill="#111" stroke="#111"/>
      <polygon points="556,383 644,383 656,420 652,470 548,470 542,420" fill="var(--orange)" stroke="var(--orange)"/>
    </g>
    <g fill="none" stroke="#fff" stroke-width="3"><rect x="385" y="266" width="30" height="30"/><path d="M392 296v-10h8v10M390 266v-8h20v8M412 258v-10h14"/></g>
    <g fill="#fff"><path d="M778 280l6-16h32l6 16v18h-8v-6h-28v6h-8z"/><circle cx="786" cy="284" r="3" fill="var(--orange)"/><circle cx="814" cy="284" r="3" fill="var(--orange)"/></g>
    <path d="M482 350l-18 32h14l-8 28 22-36h-14l10-24z" fill="#fff"/>
    <path d="M746 380l-10-4 4-4 14 2 10-10c3-3 7-3 7 0s-3 4-6 7l-10 10 2 14-4 4-4-10-8 8v6l-3 3-2-8-8-2 3-3h6z" fill="#fff"/>
    <g fill="#fff"><circle cx="610" cy="404" r="11"/><circle cx="590" cy="426" r="9"/></g>
    <g fill="var(--orange)"><circle cx="610" cy="404" r="4"/><circle cx="590" cy="426" r="3"/></g>
    <g fill="none" stroke="var(--orange)" stroke-width="1.5">
      <path d="M342 322c-30 20-50-10-28-20 20-8 20 40-60 32l-8-8m0 8l6-8"/>
      <path d="M410 304c-10 20-60-10-80 30l-4 18m0 0l-5-6m5 6l4-6"/>
      <path d="M600 476c-10 20 20 20 10 40h-6m6 0l2-8"/>
      <path d="M732 440c10 40 50 50 60 26s-30-10-20 30l6 8m0 0v-8m0 8l-8-2"/>
      <path d="M842 318c30 10 40-30 60-10l20 10m0 0l-8-2m8 2l-4 8"/>
    </g>
    <text class="sector-label" x="186" y="326">Construction</text>
    <text class="sector-label" x="912" y="336">Automotive</text>
    <text class="sector-label" x="287" y="494">Electrical</text>
    <text class="sector-label" x="516" y="561">Machinery Industries</text>
    <text class="sector-label" x="831" y="565">Aerospace</text>
  </svg>
</section>

<section>
  <div class="abs contact-info">
    <h2 class="display">Contact <span class="accent">Details</span></h2>
    <p class="lead">Ut wisi enim ad minim v quis nostrud exerci tat ullamcorper.</p>
    <div class="info-item">
      <span class="info-icon"><svg width="18" height="24" viewBox="0 0 18 24"><path d="M9 0a9 9 0 0 0-9 9c0 7 9 15 9 15s9-8 9-15a9 9 0 0 0-9-9zm0 12a3 3 0 1 1 0-6 3 3 0 0 1 0 6z" fill="var(--orange)"/></svg></span>
      <div><h3>ADDRESS</h3><p>118 Larkspur Ave, Casper,<br>WY 82601</p></div>
    </div>
    <div class="info-item">
      <span class="info-icon"><svg width="22" height="16" viewBox="0 0 22 16"><rect width="22" height="16" rx="2" fill="var(--orange)"/><path d="M1 1l10 8 10-8" fill="none" stroke="#fff" stroke-width="1.6"/></svg></span>
      <div><h3>EMAIL</h3><p>sales@vorlandcomposites.example</p></div>
    </div>
    <div class="info-item">
      <span class="info-icon"><svg width="20" height="20" viewBox="0 0 24 24"><path fill="var(--orange)" d="M6.6 10.8a15 15 0 0 0 6.6 6.6l2.2-2.2c.3-.3.7-.4 1-.2 1.1.4 2.3.6 3.6.6.6 0 1 .4 1 1V20c0 .6-.4 1-1 1A17 17 0 0 1 3 4c0-.6.4-1 1-1h3.5c.6 0 1 .4 1 1 0 1.3.2 2.5.6 3.6.1.3 0 .7-.2 1z"/></svg></span>
      <div><h3>PHONE</h3><p>555 208 3146</p></div>
    </div>
  </div>
  <div class="abs partners"><span>PARTNERS</span><div class="partner-mark"><i></i>BLORAN</div></div>

  <svg class="abs footer-bg" width="1200" height="296" viewBox="0 0 1200 296">
    <polygon points="0,70 1200,0 1200,296 0,296" fill="var(--dark)"/>
  </svg>

  <form class="abs quick-contact">
    <h2 class="display">Quick <span class="accent">Contact</span></h2>
    <div class="field"><label>Name</label><span class="ph">Jordan Blake</span><i class="ico"></i></div>
    <div class="field"><label>Email</label><span class="ph">hello@jordanblake.example</span><i class="ico"></i></div>
    <div class="field"><label>Phone</label><span class="ph">123 456 7890</span><i class="ico"></i></div>
    <div class="field message"><label>Message</label><span class="ph">Enter your message</span><i class="ico"></i></div>
    <a class="btn">Submit now</a>
  </form>
</section>

<footer>
  <nav class="abs footer-nav"><span>HOME</span><span>PRODUCTS</span><span>CONTACT US</span></nav>
  <div class="abs footer-brand">
    <span class="brand-dot"></span>
    <span class="brand-name">VORLAND</span>
    <span class="brand-divider"></span>
    <span class="brand-tag">Northgate Provisioning Trade Holdings</span>
  </div>
  <div class="abs follow">FOLLOW US:<i class="on"></i><i></i><i></i><i></i></div>
  <div class="abs footer-rule"></div>
  <p class="abs copyright">© 2025 VORLAND. All Rights Reserved.</p>
</footer>

</body>
</html>
```